Accountability Project Graphics

I want to create 10 social media graphics (new Instagram size 4:5 (1080 x 1350 pixels) focusing on our Quilvo Accountability App, using any of the 3 pictures attached. Use the attached pics only, NO RANDOM STOCK PHOTOGRAPHY. For the color scheme, use the landing page colors/fonts (attached).
You can add any of the 3 photos attached but I mainly need BOLD text that includes these headlines and sub-headlines on them.
Please NOTE for all the headlines below, also add this sub-headline on each graphic:
Stay Consistent with RT in Your Pocket!
Here are the headlines:
• Stop Starting Over Every Monday
• You don't need more willpower. You need more support
• Built for women who are tired of doing this alone
• When Motivation Fades, RT Checks In
• The Support System You've Been Missing
• Support When Motivation Disappears
• What if RT Checked in Every Day?
• The Missing Piece Isn't Another Diet
• Eat the food you love. Stay accountable every day.
• One Bad Meal Doesn't Mean You Failed
women over 40 trying to lose weight

```html
<!DOCTYPE html>
<html lang="en">
<head>
<meta charset="utf-8">
<title>Accountability App Social Graphics</title>
<link rel="stylesheet" href="https://fonts.googleapis.com/css2?family=Gelasio:ital,wght@0,700;1,700&family=Poppins:wght@500;600&display=swap">
<style>
  :root {
    --rose: #c9587f;
    --plum: #2a1a3d;
    --plum-band: #5a4466;
    --blush: #f7dbe4;
    --blush-light: #fbeef2;
    --lilac: #ecd6ef;
    --white: #ffffff;
  }
  * { box-sizing: border-box; margin: 0; padding: 0; }
  html, body { width: 1200px; height: 1011px; overflow: hidden; background: var(--white); }
  .board { position: relative; width: 1200px; height: 1011px; }
  .post {
    position: absolute; width: 363px; height: 454px; overflow: hidden;
    background: linear-gradient(160deg, var(--blush) 0%, var(--blush-light) 45%, var(--blush) 100%);
    font-family: "Gelasio", Georgia, serif; font-weight: 700;
  }
  .post--alone { background: linear-gradient(180deg, var(--blush-light) 0%, var(--lilac) 60%, #e6c5ea 100%); }
  .photo { position: absolute; }
  .photo--duo { background: linear-gradient(180deg, rgba(60,45,55,0) 0%, #3b4d6e 30%, #2f3f5c 70%, #e9d3dc 100%); border-radius: 40% 40% 0 0; opacity: .9; }
  .photo--coach { background: linear-gradient(180deg, rgba(30,25,35,0) 0%, #1e1a26 18%, #232635 100%); border-radius: 45% 45% 0 0; }
  .photo--hug { background: linear-gradient(180deg, rgba(236,214,239,0) 0%, #d9a7c8 30%, #c7739a 60%, #eee7a8 100%); }
  .headline { position: absolute; line-height: 1; }
  .rose { color: var(--rose); }
  .plum { color: var(--plum); }
  .light { color: var(--white); }
  .italic { font-style: italic; }
  .tagline { position: absolute; font-family: "Poppins", Arial, sans-serif; }
  .tagline .lead { display: block; font-size: 10.5px; font-weight: 500; color: var(--plum); }
  .tagline .brand { display: block; font-size: 14px; font-weight: 600; color: var(--rose); margin-top: 3px; }
  .count { position: absolute; left: 987px; top: 953px; font-family: "Poppins", Arial, sans-serif; font-size: 12px; color: var(--plum); }
</style>
</head>
<body>
<main class="board">

  <!-- Daily check-in -->
  <section class="post" style="left:31px; top:43px;">
    <div class="photo photo--duo" role="img" aria-label="Photo of two smiling women in denim standing together" style="left:40px; top:150px; width:290px; height:304px;"></div>
    <div class="headline" style="left:0; top:20px; width:363px; text-align:center;">
      <div class="rose" style="font-size:40px;">What If</div>
      <div class="plum italic" style="font-size:50px; margin-top:2px;">RT Checked</div>
      <div class="rose" style="font-size:40px; margin-top:2px;">in Every Day?</div>
    </div>
    <p class="tagline" style="left:0; top:400px; width:363px; text-align:center;">
      <span class="lead">Stay Consistent with</span><span class="brand">RT in Your Pocket!</span>
    </p>
  </section>

  <!-- Monday restart -->
  <section class="post" style="left:413px; top:43px;">
    <div class="photo photo--coach" role="img" aria-label="Photo of a smiling woman in a black lace top, hand on hip" style="left:204px; top:10px; width:159px; height:444px;"></div>
    <div class="headline" style="left:16px; top:62px;">
      <div class="rose" style="font-size:50px;">Stop</div>
      <div class="plum" style="font-size:39px;">Starting</div>
      <div class="rose" style="font-size:50px;">Over</div>
      <div class="rose" style="font-size:50px;">Every</div>
      <div class="plum" style="font-size:39px;">Monday</div>
    </div>
    <p class="tagline" style="left:16px; top:314px;">
      <span class="lead">Stay Consistent with</span><span class="brand">RT in Your Pocket!</span>
    </p>
  </section>

  <!-- Motivation disappears -->
  <section class="post" style="left:795px; top:43px;">
    <div class="photo photo--duo" role="img" aria-label="Photo of two smiling women in denim standing together" style="left:0; top:150px; width:280px; height:304px;"></div>
    <div class="headline" style="right:16px; top:20px; text-align:right;">
      <div style="font-size:40px;"><span class="rose">Support</span> <span class="plum italic">When</span></div>
      <div class="plum italic" style="font-size:50px; margin-top:2px;">Motivation</div>
      <div class="rose" style="font-size:40px; margin-top:2px;">Disappears</div>
    </div>
    <p class="tagline" style="right:16px; top:158px; text-align:right;">
      <span class="lead">Stay Consistent with</span><span class="brand">RT in Your Pocket!</span>
    </p>
  </section>

  <!-- Not alone -->
  <section class="post post--alone" style="left:234px; top:518px;">
    <div class="photo photo--hug" role="img" aria-label="Photo of two women hugging and laughing in a store" style="left:0; top:157px; width:363px; height:297px;"></div>
    <div class="headline" style="left:0; top:18px; width:363px; text-align:center;">
      <div class="plum" style="font-size:34px;">Built For Women</div>
      <div class="rose italic" style="font-size:28px; margin-top:2px;">Who Are Tired Of</div>
      <div class="plum" style="font-size:38px; margin-top:2px;">Doing This</div>
      <div class="plum" style="font-size:38px;">Alone</div>
    </div>
    <p class="tagline" style="left:0; top:400px; width:363px; text-align:center;">
      <span class="lead">Stay Consistent with</span><span class="brand">RT in Your Pocket!</span>
    </p>
  </section>

  <!-- Motivation fades -->
  <section class="post" style="left:616px; top:518px;">
    <svg style="position:absolute; left:0; top:0;" width="363" height="454" viewBox="0 0 363 454" aria-hidden="true">
      <polygon points="175,44 350,30 350,128 175,148" fill="#fdf3f6" opacity=".9"/>
      <polygon points="172,140 363,112 363,216 172,186" fill="var(--plum-band)"/>
      <polygon points="180,290 363,266 363,380 180,350" fill="var(--plum-band)"/>
    </svg>
    <div class="photo photo--coach" role="img" aria-label="Photo of a smiling woman in a black lace top, hand on hip" style="left:0; top:17px; width:168px; height:437px;"></div>
    <div class="headline rose" style="left:172px; top:54px; width:185px; text-align:center; font-size:48px;">When</div>
    <div class="headline light" style="left:172px; top:150px; width:191px; text-align:center; font-size:26px;">Motivation</div>
    <div class="headline rose" style="left:172px; top:210px; width:191px; text-align:center; font-size:48px;">Fades</div>
    <div class="headline light" style="left:172px; top:294px; width:191px; text-align:center; font-size:26px;">RT<br>Checks In</div>
    <p class="tagline" style="left:172px; top:392px; width:191px; text-align:center;">
      <span class="lead">Stay Consistent with</span><span class="brand">RT in Your Pocket!</span>
    </p>
  </section>

  <span class="count">x10</span>
</main>
</body>
</html>
```